Business card for law firm

Need business card for new law firm. Think confident, authoritative, conservative, but not stuffy or old-fashioned.

Contact Information for Business Card

Content for card - logo (uploaded), plus the following:

Paul Whitcombe (larger font)
Managing Partner (larger font, but not as large as name)
Level 9, 7 Ferris Lane
Sydney NSW 2000
Main Tel 02 9364 2710
Direct Tel 02 8472 3159
Email paul@qvlegal.com.au
www.qvlegal.com.au

Letterhead design should include logo plus:
Level 9, 7 Ferris Lane
Sydney NSW 2000
Tel 02 8472 3159
www.qvlegal.com.au

```html
<!DOCTYPE html>
<html lang="en">
<head>
<meta charset="utf-8">
<title>Quayvale Legal – Business Card</title>
<link rel="stylesheet" href="https://fonts.googleapis.com/css2?family=Marcellus&family=Jost:wght@400;600&display=swap">
<style>
  :root {
    --backdrop: #5b5c60;
    --navy: #0c1f5e;
    --navy-deep: #081849;
    --paper: #e9e9eb;
    --ink: #1d1d22;
    --white: #ffffff;
    --serif: "Marcellus", "Times New Roman", serif;
    --sans: "Jost", "Futura", Arial, sans-serif;
  }
  * { box-sizing: border-box; margin: 0; padding: 0; }
  html, body { width: 1200px; height: 1000px; overflow: hidden; }
  body { background: var(--backdrop); position: relative; font-family: var(--sans); }

  .card {
    position: absolute;
    width: 760px;
    height: 420px;
    border-radius: 26px;
    overflow: hidden;
  }
  .card--front { left: 220px; top: 60px; background: var(--navy); }
  .card--back  { left: 220px; top: 520px; background: var(--paper); }

  .card__band { position: absolute; inset: 0; width: 100%; height: 100%; }

  .brand { position: absolute; text-align: center; }
  .brand__mark {
    display: block; margin: 0 auto 14px;
    width: 44px; height: 44px;
  }
  .brand__name {
    font-family: var(--serif);
    font-size: 54px;
    letter-spacing: 3px;
    line-height: 1;
  }
  .brand__tag {
    font-family: var(--serif);
    font-size: 17px;
    letter-spacing: 22px;
    margin-top: 6px;
    padding-left: 22px;
  }

  .card--front .brand { left: 340px; top: 90px; width: 360px; color: var(--white); }
  .card--front .brand__mark { background: var(--white); }
  .front__web {
    position: absolute; left: 340px; width: 360px; top: 330px;
    text-align: center; color: var(--white);
    font-size: 17px; letter-spacing: 1px;
  }

  .card--back .brand { left: 330px; top: 50px; width: 340px; color: var(--ink); }
  .card--back .brand__mark { background: var(--navy); }
  .card--back .brand__name { font-size: 48px; }
  .card--back .brand__tag { font-size: 15px; letter-spacing: 19px; }

  .contact {
    position: absolute; left: 330px; top: 228px;
    color: var(--ink); font-size: 15.5px; line-height: 1.55;
  }
  .contact__name {
    font-size: 22px; font-weight: 600; color: var(--navy);
    letter-spacing: .5px; text-transform: uppercase;
  }
  .contact__role { font-size: 16px; margin-left: 6px; }
  .contact__label { font-weight: 600; color: var(--navy); }
  .contact__row { display: flex; align-items: center; gap: 6px; }
  .contact__gap { margin-left: 14px; }
  .icon { width: 14px; height: 14px; fill: var(--navy); flex: none; }
  .contact__web b { color: var(--navy); font-weight: 600; }
</style>
</head>
<body>

  <section class="card card--front" aria-label="Card front">
    <svg class="card__band" viewBox="0 0 760 420" preserveAspectRatio="none" aria-hidden="true">
      <path d="M0 0 H250 C300 120 300 300 230 420 H0 Z" fill="var(--navy-deep)"/>
    </svg>
    <div class="brand">
      <span class="brand__mark"></span>
      <div class="brand__name">QUAYVALE</div>
      <div class="brand__tag">LEGAL</div>
    </div>
    <div class="front__web">www.qvlegal.com.au</div>
  </section>

  <section class="card card--back" aria-label="Card back">
    <svg class="card__band" viewBox="0 0 760 420" preserveAspectRatio="none" aria-hidden="true">
      <path d="M0 0 H190 C250 130 250 300 200 420 H0 Z" fill="var(--navy)"/>
    </svg>
    <div class="brand">
      <span class="brand__mark"></span>
      <div class="brand__name">QUAYVALE</div>
      <div class="brand__tag">LEGAL</div>
    </div>
    <div class="contact">
      <div><span class="contact__name">Paul Whitcombe</span><span class="contact__role">Managing Partner</span></div>
      <div>Level 9, 7 Ferris Lane Sydney NSW 2000</div>
      <div><span class="contact__label">Main Tel</span> 02 9364 2710 <span class="contact__label contact__gap">Direct Tel</span> 02 8472 3159</div>
      <div class="contact__row">
        <svg class="icon" viewBox="0 0 16 16" aria-hidden="true"><path d="M1 3h14v10H1z M1 3l7 6 7-6" fill="none" stroke="var(--navy)" stroke-width="1.6"/></svg>
        <span>paul@qvlegal.com.au</span>
        <svg class="icon contact__gap" viewBox="0 0 16 16" aria-hidden="true"><circle cx="8" cy="8" r="6.5" fill="none" stroke="var(--navy)" stroke-width="1.4"/><path d="M1.5 8h13 M8 1.5c-3 3.5-3 9.5 0 13 M8 1.5c3 3.5 3 9.5 0 13" fill="none" stroke="var(--navy)" stroke-width="1.1"/></svg>
        <span class="contact__web">www.<b>qvlegal</b>.com.au</span>
      </div>
    </div>
  </section>

</body>
</html>
```